Business card design for a dynamic IT consulting company

We need a business card design for a young firm, specialized in the Telecommunications/Consulting industry. The name of the company is Quindor and Partners Business Consulting Ltd. (Short name: Quindor and Partnes)
Quindor = solve read reverse, so we aim to be uncomplicated and solution-oriented. The small pipe in our logo is also related to the word solve. So we need a new business card design, which is simple, eye catching and something non traditional (I would probably prefer a square shaped design rather than a rectangle, but open for suggestions). Attached our logo.

Target Market(s)

Usually our customers are Tier1 Telecoms providers (Q-Netra, Palorix, etc) and their executives.

Industry/Entity Type

Business

Contact Information for Business Card

Name: Bence Tolnavari
Email: b.tolnavari@quindor.hu
Web: www.quindor.hu
Mobile: +36 30 518 2769
Title: Managing Director

Optional:
Company name: Quindor and Partners Ltd.
Address: 1087 Budapest, Tolvenka str. 28/C, Hungary

Font styles to use
Other font styles liked:
• helveticaneue_medium, Prime Regular are used now.

Colors

Designer to choose colors to be used in the design.

Requirements
Must have
• I would like to have a 2 sided design.
Nice to have
• I thought if we make the logo a bit bigger (without the company name), that could go to the back with the company name below. I though, if the pipe in the logo is somehow touchable on the business card, would be nice and unique.

```html
<!DOCTYPE html>
<html lang="en">
<head>
<meta charset="utf-8">
<title>Quindor and Partners – Business Card</title>
<link rel="stylesheet" href="https://fonts.googleapis.com/css2?family=Open+Sans:wght@400;700&display=swap">
<style>
  :root {
    --stage: #e9e9e9;
    --card-dark: #545557;
    --card-light: #ffffff;
    --ink: #4a4a4c;
    --brand-blue: #1a9ad6;
    --tint-blue: #d6ebf6;
    --tint-pink: #f2dcea;
    --tint-grey: #ececec;
    --on-dark: #ffffff;
  }
  * { box-sizing: border-box; margin: 0; padding: 0; }
  html, body { width: 1200px; height: 900px; overflow: hidden; }
  body {
    background: var(--stage);
    font-family: "Open Sans", Arial, sans-serif;
    position: relative;
  }
  .card {
    position: absolute;
    width: 640px;
    height: 366px;
    border-radius: 4px;
    box-shadow: 0 6px 18px rgba(0,0,0,.18);
    overflow: hidden;
  }
  .card--front {
    left: 90px; top: 80px;
    background: var(--card-dark);
    display: flex; align-items: center; justify-content: center;
  }
  .card--back { left: 470px; top: 470px; background: var(--card-light); }

  .card__pattern { position: absolute; inset: 0; }
  .card--back .card__pattern {
    background:
      radial-gradient(circle at 85% 25%, var(--tint-blue) 0, transparent 38%),
      radial-gradient(circle at 70% 80%, var(--tint-pink) 0, transparent 35%),
      radial-gradient(circle at 50% 10%, var(--tint-grey) 0, transparent 30%);
  }

  .wordmark {
    display: flex;
    align-items: center;
    gap: 12px;
    font-weight: 400;
    font-size: 42px;
    line-height: 1;
    white-space: nowrap;
  }
  .wordmark__square { width: 14px; height: 14px; background: var(--brand-blue); flex: none; }
  .card--front .wordmark { color: var(--on-dark); }
  .card--back .wordmark { position: absolute; left: 46px; top: 88px; color: var(--ink); }

  .person { position: absolute; left: 70px; top: 212px; }
  .person__name {
    font-size: 20px; font-weight: 700; color: var(--brand-blue);
    letter-spacing: .5px; text-transform: uppercase;
  }
  .person__title { font-size: 15px; color: var(--ink); }

  .contacts { list-style: none; margin-top: 10px; }
  .contacts__item {
    display: flex; align-items: center; gap: 8px;
    font-size: 15px; color: var(--ink); line-height: 24px;
  }
  .contacts__icon { width: 14px; height: 14px; flex: none; }

  .address {
    position: absolute; right: 40px; top: 178px;
    text-align: right; font-size: 13px; line-height: 18px; color: var(--ink);
  }
  .address__company { color: var(--brand-blue); }
</style>
</head>
<body>

  <section class="card card--front" aria-label="Card front">
    <div class="wordmark"><span class="wordmark__square"></span>Quindor and Partners</div>
  </section>

  <section class="card card--back" aria-label="Card back">
    <div class="card__pattern" role="img" aria-label="Scattered pastel squares decoration"></div>

    <div class="wordmark"><span class="wordmark__square"></span>Quindor and Partners</div>

    <div class="address">
      <div class="address__company">Quindor and Partners Ltd</div>
      <div>1087 Budapest, Tolvenka</div>
      <div>str. 28/C, Hungary</div>
    </div>

    <div class="person">
      <div class="person__name">Bence Tolnavari</div>
      <div class="person__title">Managing Director</div>
      <ul class="contacts">
        <li class="contacts__item">
          <svg class="contacts__icon" viewBox="0 0 16 16" aria-hidden="true"><path fill="#1a9ad6" d="M3 2h3l1.5 3.5-2 1.2a8 8 0 0 0 3.8 3.8l1.2-2L14 10v3a1 1 0 0 1-1 1A11 11 0 0 1 2 3a1 1 0 0 1 1-1z"/></svg>
          +36 30 518 2769
        </li>
        <li class="contacts__item">
          <svg class="contacts__icon" viewBox="0 0 16 16" aria-hidden="true"><rect x="1" y="3" width="14" height="10" rx="1" fill="#1a9ad6"/><path d="M1.5 3.5 8 9l6.5-5.5" stroke="#fff" stroke-width="1.3" fill="none"/></svg>
          b.tolnavari@quindor.hu
        </li>
        <li class="contacts__item">
          <svg class="contacts__icon" viewBox="0 0 16 16" aria-hidden="true"><circle cx="8" cy="8" r="7" fill="#1a9ad6"/><path d="M1.5 8h13M8 1.2c2.5 2.6 2.5 11 0 13.6M8 1.2c-2.5 2.6-2.5 11 0 13.6" stroke="#fff" stroke-width="1" fill="none"/></svg>
          www.quindor.hu
        </li>
      </ul>
    </div>
  </section>

</body>
</html>
```